Website Design for The Elder Nook

Please design and code a new website.
Here are the sites I like best:
http://www.voyaglint.com/alternate/
http://www.wheelgiftbay.org
Please make it similar but look at the competitor site (below) for images and wording. This is NOT a car donation site. It's a senior lead placement site like https://www.kinhavenfinder.com. I just like this sites above as a lead generation sites.
Competitor site:
https://www.kinhavenfinder.com (use ideas / verbiage from this site)
Updates
Competitor site:
Coding
Coded - Design and coding required
Number of Pages Required
1 page
Look and feel
Each slider illustrates characteristics of the customer's brand and the style your logo design should communicate.

```html
<!DOCTYPE html>
<html lang="en">
<head>
<meta charset="utf-8">
<title>The Elder Nook — Senior Living Advisors</title>
<link rel="stylesheet" href="https://fonts.googleapis.com/css2?family=Montserrat:wght@400;500;600;700;800&display=swap">
<style>
:root{
  --navy:#231c6c;
  --navy-deep:#1a1455;
  --green:#1f9d5c;
  --green-bright:#2bb36c;
  --green-dark:#14764a;
  --ink:#2a2a3a;
  --muted:#5a5a6a;
  --line:#e3e6ee;
  --white:#ffffff;
  --sky:#2f8fd6;
  --map:#2a6fc4;
}
*{box-sizing:border-box;margin:0;padding:0}
html,body{width:1200px;height:5279px;overflow:hidden}
body{font-family:"Montserrat",Arial,sans-serif;color:var(--ink);background:var(--white);position:relative}
a{color:inherit;text-decoration:none}
section,header,footer,nav{position:relative;width:1200px}
.green{color:var(--green)}

/* header */
.site-header{height:130px;background:var(--white)}
.brand{position:absolute;left:34px;top:30px;display:flex;align-items:center;gap:12px}
.brand-dot{width:40px;height:40px;border-radius:50%;background:var(--green)}
.brand-name{font-size:28px;font-weight:700;color:var(--navy)}
.header-phone{position:absolute;right:40px;top:22px;display:flex;align-items:center;gap:12px}
.phone-ring{width:44px;height:44px;border-radius:50%;border:3px solid var(--navy);display:flex;align-items:center;justify-content:center;flex:none}
.header-phone strong{display:block;font-size:26px;font-weight:800;color:var(--navy)}
.header-phone small{font-size:12px;color:var(--muted)}

.main-nav{height:38px;background:var(--navy);display:flex;align-items:center;padding-left:34px;gap:22px}
.main-nav a{color:var(--white);font-size:12px;font-weight:700;text-transform:uppercase;white-space:nowrap}
.cta-box{position:absolute;right:0;top:92px;width:432px;height:76px;background:var(--green);color:var(--white);text-align:center;font-weight:700;font-size:19px;line-height:1.3;padding-top:12px;z-index:2}

/* hero */
.hero{height:482px;background:linear-gradient(120deg,#6f8f4f 0%,#8aa86a 30%,#b7c79c 55%,#5e7d47 100%)}
.hero-photo{position:absolute;inset:0}
.lead-form{position:absolute;left:767px;top:30px;width:352px;padding:16px 22px 20px;background:rgba(31,157,92,.93)}
.field{height:36px;background:var(--white);margin-bottom:12px;font-size:12px;font-weight:600;padding:11px 12px;color:var(--ink);position:relative}
.field.select::after{content:"";position:absolute;right:14px;top:15px;border:6px solid transparent;border-top-color:var(--navy)}
.submit{display:inline-block;background:var(--navy);color:var(--white);font-size:12px;font-weight:700;padding:11px 22px;margin-top:4px}

/* support band */
.support-band{height:243px;background:linear-gradient(90deg,var(--green-dark),var(--green) 40%,var(--green-bright))}
.support-band h2{position:absolute;left:86px;top:64px;width:380px;color:var(--white);font-size:36px;font-weight:800;line-height:1.15;text-transform:uppercase}
.perks{position:absolute;left:530px;top:62px;display:flex;gap:20px}
.perk{width:104px;text-align:center;color:var(--white);font-size:12px;font-weight:600;line-height:1.35}
.perk svg{display:block;margin:0 auto 12px}

/* how it works */
.how{height:614px;text-align:center}
.section-title{font-size:32px;font-weight:800;color:var(--navy)}
.how .section-title{padding-top:100px}
.steps{position:absolute;top:190px;left:170px;display:flex;gap:92px}
.step{width:188px}
.step-photo{width:170px;height:170px;border-radius:50%;margin:0 auto 22px;border:5px solid #f0f2f6}
.step-num{font-size:26px;font-weight:800;color:var(--green)}
.step p{font-size:16px;font-weight:500;color:var(--navy);line-height:1.35}

/* no cost */
.no-cost{height:390px;background:linear-gradient(90deg,#d9ecf9 0%,#b8dcf4 35%,#6fb6e6 65%,#2f8fd6 100%)}
.no-cost .photo{position:absolute;left:80px;top:20px;width:460px;height:370px;background:linear-gradient(160deg,#e8eef4,#b9c7d4 60%,#8ea2b6)}
.no-cost-copy{position:absolute;left:690px;top:88px;width:460px;text-align:center}
.no-cost h2{font-size:38px;font-weight:800;color:var(--navy)}
.no-cost h2 span{color:var(--green)}
.no-cost p{margin-top:14px;font-size:16px;font-weight:600;color:var(--navy);line-height:1.5}
.btn-call{display:inline-block;margin-top:26px;background:var(--green);color:var(--white);font-size:26px;font-weight:700;padding:16px 34px}

/* veterans */
.veterans{height:513px}
.veterans h2{position:absolute;left:94px;top:120px;font-size:28px;font-weight:800;color:var(--navy)}
.veterans p{position:absolute;left:94px;top:198px;width:770px;font-size:18px;line-height:1.55;color:var(--muted)}
.btn-outline{position:absolute;left:94px;top:356px;background:var(--green);color:var(--white);font-size:15px;font-weight:600;padding:10px 30px}
.vet-photo{position:absolute;left:880px;top:80px;width:270px;height:270px;border-radius:50%;background:radial-gradient(circle at 40% 40%,#e3e7f2,#8da0c8 55%,#b0242f 85%)}

/* testimonials */
.testimonials{height:473px;background:linear-gradient(180deg,#2d2570,#3a3183 50%,#2b2366);color:var(--white)}
.testimonials .section-title{color:var(--white);text-align:center;padding-top:70px}
.quotes{position:absolute;top:170px;left:90px;display:flex;gap:40px}
.quote{width:310px;position:relative}
.quote-mark{position:absolute;left:-6px;top:-10px;font-size:56px;font-weight:800;color:var(--green-bright);line-height:1}
.quote-body{background:rgba(20,16,60,.55);padding:14px 16px 16px 44px;font-size:14px;line-height:1.45}
.quote-foot{display:flex;align-items:center;justify-content:space-between;margin-top:14px}
.quote-foot em{font-size:13px;font-weight:600}
.avatar{width:62px;height:62px;border-radius:50%;border:3px solid var(--white);background:#c9b8a8}
.dots{position:absolute;top:420px;left:0;width:1200px;display:flex;justify-content:center;gap:8px}
.dots i{width:10px;height:10px;border-radius:50%;border:2px solid var(--white)}
.dots i:first-child{background:var(--white)}

/* state */
.by-state{height:987px}
.by-state .section-title{text-align:center;padding-top:94px}
.view-tabs{position:absolute;top:176px;left:420px;display:flex;gap:20px}
.tab{display:flex;align-items:center;gap:14px;height:48px;padding:0 22px;border:1px solid var(--line);background:var(--white);font-size:15px;font-weight:700;color:var(--navy);box-shadow:0 2px 8px rgba(0,0,0,.08)}
.tab .ico{width:34px;height:30px;background:var(--green);display:flex;align-items:center;justify-content:center}
.tab .ico.navy{background:var(--navy);color:var(--white);font-size:10px}
.tab.active{color:var(--green)}
.care-types{position:absolute;left:90px;top:300px;width:258px}
.care-type{display:flex;align-items:center;gap:14px;height:54px;margin-bottom:14px;border:1px solid var(--line);box-shadow:0 2px 8px rgba(0,0,0,.08);font-size:16px;font-weight:600;color:var(--navy);padding-right:12px}
.care-type .ico{width:52px;height:52px;background:var(--navy);display:flex;align-items:center;justify-content:center}
.us-map{position:absolute;left:420px;top:270px;width:710px;height:560px;border-radius:18px;background:linear-gradient(160deg,#1f56a8 0%,#2a6fc4 45%,#4a93dc 80%,#7fb3e6 100%)}

/* advisor */
.advisor{height:445px;background:linear-gradient(90deg,#ffffff 45%,#f1ece6 60%)}
.advisor .photo{position:absolute;right:0;top:0;width:620px;height:445px;background:linear-gradient(120deg,#f4efe9,#e6d6c6 40%,#cfb59c 75%,#e8d9c6)}
.advisor h2{position:absolute;left:80px;top:66px;font-size:32px;font-weight:800;color:var(--navy);line-height:1.25}
.advisor p.lead{position:absolute;left:80px;top:178px;width:470px;font-size:17px;font-weight:600;line-height:1.5;color:var(--ink)}
.advisor ul{position:absolute;left:80px;top:268px;list-style:none}
.advisor li{display:flex;align-items:center;gap:16px;font-size:17px;font-weight:600;color:var(--navy);margin-bottom:16px}

/* city lists */
.city-lists{height:521px;display:flex;padding:60px 0 0 80px}
.city-col{width:380px}
.city-col h3{font-size:18px;font-weight:800;color:var(--navy);margin-bottom:14px}
.city-col li{list-style:none;font-size:13px;line-height:1.45;color:var(--ink)}

/* footer */
.site-footer{height:391px;background:linear-gradient(180deg,#241c6e,#1e1862);color:var(--white)}
.footer-brand{position:absolute;left:0;top:34px;width:1200px;display:flex;justify-content:center;align-items:center;gap:12px}
.footer-brand .brand-dot{background:var(--green-bright)}
.footer-brand span{font-size:28px;font-weight:700;color:var(--white)}
.footer-col{position:absolute;top:160px}
.footer-col h4{font-size:13px;font-weight:800;color:var(--green-bright);text-transform:uppercase;margin-bottom:14px}
.footer-col p,.footer-col li{font-size:13px;font-weight:600;line-height:1.5;list-style:none}
.footer-about{left:200px;width:190px}
.footer-links{left:500px;width:200px}
.footer-contact{left:720px;top:150px;display:flex;gap:14px;align-items:flex-start}
.footer-contact .phone-ring{border-color:var(--white)}
.footer-contact strong{font-size:28px;font-weight:800;display:block}
.footer-contact small{font-size:12px}
.socials{display:flex;gap:8px;margin-top:16px}
.socials i{width:34px;height:34px;background:var(--sky);display:block}
.copyright{height:52px;background:var(--white);text-align:center;font-size:12px;font-weight:700;color:var(--ink);padding-top:18px;border-top:1px solid var(--line)}
</style>
</head>
<body>

<header class="site-header">
  <a class="brand" href="#"><span class="brand-dot"></span><span class="brand-name">The Elder Nook</span></a>
  <div class="header-phone">
    <span class="phone-ring"><svg width="22" height="22" viewBox="0 0 24 24"><path d="M6.6 10.8a15.1 15.1 0 0 0 6.6 6.6l2.2-2.2a1 1 0 0 1 1-.25 11.4 11.4 0 0 0 3.6.57 1 1 0 0 1 1 1V20a1 1 0 0 1-1 1A17 17 0 0 1 3 4a1 1 0 0 1 1-1h3.5a1 1 0 0 1 1 1c0 1.25.2 2.45.57 3.57a1 1 0 0 1-.25 1z" fill="#231c6c"/></svg></span>
    <div><strong>1-800-555-0142</strong><small>Talk Today to a Local Advisor for FREE</small></div>
  </div>
</header>

<nav class="main-nav">
  <a href="#">Assisted Living</a><a href="#">Memory Care</a><a href="#">Nursing Homes</a><a href="#">More Living Options ▾</a><a href="#">Planning &amp; Advice</a>
</nav>
<div class="cta-box">You know your family. We know<br>Senior Living. Contact us now!</div>

<section class="hero">
  <div class="hero-photo" role="img" aria-label="Photo of a senior couple walking arm in arm through a green park"></div>
  <form class="lead-form">
    <div class="field">First Name*</div>
    <div class="field">Last Name*</div>
    <div class="field">Primary Phone*</div>
    <div class="field">Cell Phone*</div>
    <div class="field">Email*</div>
    <div class="field select">State*</div>
    <span class="submit">SUBMIT</span>
  </form>
</section>

<section class="support-band">
  <h2>The support you need to make the right choice</h2>
  <div class="perks">
    <div class="perk"><svg width="48" height="48" viewBox="0 0 48 48" fill="none" stroke="#fff" stroke-width="3"><circle cx="20" cy="16" r="9"/><path d="M4 44c2-10 8-14 16-14s14 4 16 14"/><path d="M34 10h10v8h-6l-4 3z"/></svg>Dedicated local advisor</div>
    <div class="perk"><svg width="48" height="48" viewBox="0 0 48 48" fill="none" stroke="#fff" stroke-width="3"><path d="M4 44V20L24 6l20 14v24z"/><rect x="18" y="28" width="12" height="16"/><rect x="10" y="22" width="6" height="6"/><rect x="32" y="22" width="6" height="6"/></svg>Hand-picked list of communities</div>
    <div class="perk"><svg width="48" height="48" viewBox="0 0 48 48" fill="none" stroke="#fff" stroke-width="3"><path d="M10 4h20l10 10v30H10z"/><path d="M30 4v10h10M16 24h18M16 31h18M16 38h12"/></svg>Full details and pricing</div>
    <div class="perk"><svg width="48" height="48" viewBox="0 0 48 48" fill="none" stroke="#fff" stroke-width="3"><rect x="5" y="9" width="38" height="34"/><path d="M5 18h38M14 4v10M34 4v10"/><path d="M13 26h6M21 26h6M29 26h6M13 34h6M21 34h6"/></svg>Help scheduling tours</div>
    <div class="perk"><svg width="48" height="48" viewBox="0 0 48 48" fill="none" stroke="#fff" stroke-width="3"><path d="M4 30l4-12h28l8 12v8H4z"/><circle cx="13" cy="38" r="4"/><circle cx="35" cy="38" r="4"/><path d="M12 18l2-6h18l2 6"/></svg>Move-in support</div>
  </div>
</section>

<section class="how">
  <h2 class="section-title">How Our <span class="green">Service Works</span></h2>
  <div class="steps">
    <div class="step"><div class="step-photo" role="img" aria-label="Photo of a friendly advisor wearing a headset" style="background:linear-gradient(140deg,#e8edf2,#c7b39f 60%,#a8927e)"></div><div class="step-num">01.</div><p>Talk with your<br>local advisor</p></div>
    <div class="step"><div class="step-photo" role="img" aria-label="Photo of an advisor sharing information with an older adult" style="background:linear-gradient(140deg,#dfe6ec,#a9b6c4 60%,#7f8fa0)"></div><div class="step-num">02.</div><p>Get information<br>on care options</p></div>
    <div class="step"><div class="step-photo" role="img" aria-label="Photo of a senior community hallway with residents" style="background:linear-gradient(140deg,#eee8de,#c9b89e 60%,#8c9c7a)"></div><div class="step-num">03.</div><p>Select communities<br>to visit</p></div>
    <div class="step"><div class="step-photo" role="img" aria-label="Photo of a senior settling into a new home" style="background:linear-gradient(140deg,#e9e4dc,#b9a58d 60%,#8f7b66)"></div><div class="step-num">04.</div><p>Transition to<br>new home</p></div>
  </div>
</section>

<section class="no-cost">
  <div class="photo" role="img" aria-label="Photo of a joyful senior man with arms stretched wide outdoors"></div>
  <div class="no-cost-copy">
    <h2>There's <span>No Cost</span> to You</h2>
    <p>We work with over 20,000 senior living communities. Our community partners pay us for placement services.</p>
    <a class="btn-call" href="#">Call 1-800-555-0142</a>
  </div>
</section>

<section class="veterans">
  <h2>Access up to $2,000 per Month <span class="green">in Veteran's Aid</span></h2>
  <p>We work with Veterans every day. Most veteran families do not know of a key benefit available to them and their families. It's called the Veteran's Aid and Attendance benefit. This benefit can help pay for senior living and home care.</p>
  <a class="btn-outline" href="#">Learn More</a>
  <div class="vet-photo" role="img" aria-label="Photo of a saluting veteran in front of a flag"></div>
</section>

<section class="testimonials">
  <h2 class="section-title">97% of Our Customers Recommend Our Service</h2>
  <div class="quotes">
    <div class="quote"><span class="quote-mark">“</span><div class="quote-body">Our advisor listened closely and found a lovely place for my mother within a week. The whole family feels at peace with the choice we made.</div><div class="quote-foot"><em>Carol Whitman</em><span class="avatar" role="img" aria-label="Portrait of the reviewer"></span></div></div>
    <div class="quote"><span class="quote-mark">“</span><div class="quote-body">We had no idea where to begin. Our advisor toured homes with us, explained costs, and helped Dad settle into memory care with real kindness.</div><div class="quote-foot"><em>Elena Brandt</em><span class="avatar" role="img" aria-label="Portrait of the reviewer"></span></div></div>
    <div class="quote"><span class="quote-mark">“</span><div class="quote-body">Quick answers, honest pricing and patient support from the first call. I would recommend this free service to any family facing the same decision.</div><div class="quote-foot"><em>Jonah Hale</em><span class="avatar" role="img" aria-label="Portrait of the reviewer"></span></div></div>
  </div>
  <div class="dots"><i></i><i></i><i></i><i></i></div>
</section>

<section class="by-state">
  <h2 class="section-title">Senior Living <span class="green">by State</span></h2>
  <div class="view-tabs">
    <div class="tab active"><span class="ico"><svg width="18" height="14" viewBox="0 0 18 14"><path d="M0 2l6-2 6 2 6-2v12l-6 2-6-2-6 2z" fill="#fff"/></svg></span>VIEW BY MAP ◂</div>
    <div class="tab"><span class="ico navy">A-Z</span>VIEW BY ALPHABET</div>
  </div>
  <div class="care-types">
    <div class="care-type"><span class="ico"><svg width="24" height="24" viewBox="0 0 24 24" fill="#fff"><circle cx="8" cy="5" r="3"/><circle cx="16" cy="5" r="3"/><rect x="5" y="9" width="6" height="13"/><rect x="13" y="9" width="6" height="13"/></svg></span>Assisted Living</div>
    <div class="care-type"><span class="ico"><svg width="24" height="24" viewBox="0 0 24 24" fill="none" stroke="#fff" stroke-width="2"><circle cx="12" cy="10" r="7"/><path d="M9 22h6M12 17v5"/></svg></span>Memory Care</div>
    <div class="care-type"><span class="ico"><svg width="24" height="24" viewBox="0 0 24 24" fill="#fff"><circle cx="12" cy="4" r="3"/><rect x="9" y="8" width="6" height="14"/></svg></span>Independent Living</div>
    <div class="care-type"><span class="ico"><svg width="24" height="24" viewBox="0 0 24 24" fill="#fff"><path d="M10 3h4v7h7v4h-7v7h-4v-7H3v-4h7z"/></svg></span>Nursing Home</div>
    <div class="care-type"><span class="ico"><svg width="24" height="24" viewBox="0 0 24 24" fill="#fff"><path d="M12 2l10 9h-3v11H5V11H2z"/></svg></span>Care Homes</div>
  </div>
  <div class="us-map" role="img" aria-label="Clickable map of the United States, including Alaska and Hawaii, for choosing a state"></div>
</section>

<section class="advisor">
  <div class="photo" role="img" aria-label="Photo of a smiling senior woman embraced by her adult daughter"></div>
  <h2>Your local advisor.<br><span class="green">You decide.</span></h2>
  <p class="lead">Over 400 senior advisors across the U.S. and Canada are ready to help your family with:</p>
  <ul>
    <li><svg width="22" height="22" viewBox="0 0 24 24" fill="#231c6c"><path d="M12 2a7 7 0 0 0-7 7c0 5 7 13 7 13s7-8 7-13a7 7 0 0 0-7-7zm0 9.5A2.5 2.5 0 1 1 12 6.5a2.5 2.5 0 0 1 0 5z"/></svg>Insider's tips for the area near you</li>
    <li><svg width="22" height="22" viewBox="0 0 24 24" fill="none" stroke="#231c6c" stroke-width="2"><circle cx="9" cy="8" r="4"/><path d="M2 21c1-5 4-7 7-7s6 2 7 7M17 4h5v5"/></svg>Advice tailored to your unique situation</li>
    <li><svg width="22" height="22" viewBox="0 0 24 24" fill="none" stroke="#231c6c" stroke-width="2"><circle cx="12" cy="12" r="10"/><path d="M12 6v6l4 2"/></svg>Time saving know-how and resources</li>
  </ul>
</section>

<section class="city-lists">
  <div class="city-col">
    <h3>Independent Living</h3>
    <ul>
      <li>New York Independent Living</li><li>Los Angeles Independent Living</li><li>Chicago Independent Living</li><li>Dallas Independent Living</li><li>Houston Independent Living</li><li>Washington DC Independent Living</li><li>Philadelphia Independent Living</li><li>Miami Independent Living</li><li>Atlanta Independent Living</li><li>Boston Independent Living</li><li>San Francisco Independent Living</li><li>Phoenix Independent Living</li><li>Orange County Independent Living</li><li>Detroit Independent Living</li><li>Seattle Independent Living</li><li>Minneapolis Independent Living</li><li>San Diego Independent Living</li><li>Tampa Independent Living</li><li>Denver Independent Living</li><li>St. Louis Independent Living</li><li>Baltimore Independent Living</li>
    </ul>
  </div>
  <div class="city-col">
    <h3>Memory <span class="green">Care</span></h3>
    <ul>
      <li>New York Memory Care</li><li>Los Angeles Memory Care</li><li>Chicago Memory Care</li><li>Dallas Memory Care</li><li>Houston Memory Care</li><li>Washington DC Memory Care</li><li>Philadelphia Memory Care</li><li>Miami Memory Care</li><li>Atlanta Memory Care</li><li>Boston Memory Care</li><li>San Francisco Memory Care</li><li>Phoenix Memory Care</li><li>Orange County Memory Care</li><li>Detroit Memory Care</li><li>Seattle Memory Care</li><li>Minneapolis Memory Care</li><li>San Diego Memory Care</li><li>Tampa Memory Care</li><li>Denver Memory Care</li><li>St. Louis Memory Care</li><li>Baltimore Memory Care</li>
    </ul>
  </div>
  <div class="city-col">
    <h3>Nursing Homes</h3>
    <ul>
      <li>New York Nursing Homes</li><li>Los Angeles Nursing Homes</li><li>Chicago Nursing Homes</li><li>Dallas Nursing Homes</li><li>Houston Nursing Homes</li><li>Washington DC Nursing Homes</li><li>Philadelphia Nursing Homes</li><li>Miami Nursing Homes</li><li>Atlanta Nursing Homes</li><li>Boston Nursing Homes</li><li>San Francisco Nursing Homes</li><li>Phoenix Nursing Homes</li><li>Orange County Nursing Homes</li><li>Detroit Nursing Homes</li><li>Seattle Nursing Homes</li><li>Minneapolis Nursing Homes</li><li>San Diego Nursing Homes</li><li>Tampa Nursing Homes</li><li>Denver Nursing Homes</li><li>St. Louis Nursing Homes</li><li>Baltimore Nursing Homes</li>
    </ul>
  </div>
</section>

<footer class="site-footer">
  <div class="footer-brand"><span class="brand-dot"></span><span>The Elder Nook</span></div>
  <div class="footer-col footer-about">
    <h4>About The Elder Nook</h4>
    <p>We guide families through every step of choosing senior living, from first questions to move-in day, at no cost to you.</p>
  </div>
  <div class="footer-col footer-links">
    <h4>Quick Links</h4>
    <ul><li>Assisted Living</li><li>Memory Care</li><li>Nursing Homes</li><li>More Living Options</li><li>Planning &amp; Advice</li><li>How Our Service Works</li></ul>
  </div>
  <div class="footer-col footer-contact">
    <span class="phone-ring"><svg width="22" height="22" viewBox="0 0 24 24"><path d="M6.6 10.8a15.1 15.1 0 0 0 6.6 6.6l2.2-2.2a1 1 0 0 1 1-.25 11.4 11.4 0 0 0 3.6.57 1 1 0 0 1 1 1V20a1 1 0 0 1-1 1A17 17 0 0 1 3 4a1 1 0 0 1 1-1h3.5a1 1 0 0 1 1 1c0 1.25.2 2.45.57 3.57a1 1 0 0 1-.25 1z" fill="#fff"/></svg></span>
    <div><strong>1-800-555-0142</strong><small>Talk Today to a Local Advisor for FREE</small>
      <div class="socials"><i></i><i></i><i></i></div>
    </div>
  </div>
</footer>
<div class="copyright">COPYRIGHT © 2019 THE ELDER NOOK. ALL RIGHTS RESERVED.</div>

</body>
</html>
```